sydney wedding photography business needs a business card design

we need a business card design for a sydney based wedding photography and videography business. our business name is :golden hour studio and film. our target clients are 24-35 yrs female. our style is candid, organic, natural, dynamic. we are a team of young photographers and videographers, and help brides to create memories that they will cherish for the rest of their lives. the logo will be provided. we want an elegant design that reflects our style, and also want to give a great impression to our clients that we are one of the best studios in sydney and our brand means quality and premium service.

Target Market(s)

bride to be, 24-35 years old, living in sydney and surrunding areas

Industry/Entity Type

Wedding Photography

Contact Information for Business Card

address: 57 tarrant street, glenmore nsw 2047
mobile: 0431872259
phone: (02) 9163 2408
info@tidewillowstudio.net.au
www.tidewillowstudio.net.au
facebook:tidewillowweddings
instagram:tidewillowweddings

Font styles to use
Serif
Sans Serif

Requirements
Nice to have
• maybe add my slogan"memories beyond eternity" if the layout looks good
Should not have
• no black color, not good idea for wedding biz card

```html
<!DOCTYPE html>
<html lang="en">
<head>
<meta charset="utf-8">
<title>Golden Hour Studio and Film – Business Card</title>
<link href="https://fonts.googleapis.com/css2?family=Dosis:wght@500;600&display=swap" rel="stylesheet">
<style>
  :root {
    --backdrop: #e6e1da;
    --card-deep: #3b2417;
    --card-mid: #5a3a26;
    --gold: #c98a2e;
    --gold-light: #e6b062;
    --gold-deep: #7d4a18;
    --ink: #4a2c14;
  }
  * { margin: 0; padding: 0; box-sizing: border-box; }
  html, body {
    width: 1200px; height: 969px; overflow: hidden;
    background: var(--backdrop);
    font-family: "Dosis", "Arial Narrow", sans-serif;
  }
  .business-card {
    position: absolute; left: 100px; top: 200px;
    width: 1000px; height: 570px;
    background: radial-gradient(ellipse 70% 60% at 50% 45%, var(--card-mid), var(--card-deep) 80%);
    box-shadow: 0 18px 40px rgba(60,36,20,0.25);
    overflow: hidden;
  }
  .corner { position: absolute; width: 44px; height: 44px; border: 0 solid var(--gold); }
  .corner--tl { left: 22px; top: 12px; border-left-width: 3px; border-top-width: 3px; }
  .corner--tr { right: 22px; top: 12px; border-right-width: 3px; border-top-width: 3px; }
  .corner--bl { left: 22px; top: 346px; border-left-width: 3px; border-bottom-width: 3px; }
  .corner--br { right: 22px; top: 346px; border-right-width: 3px; border-bottom-width: 3px; }
  .brand {
    position: absolute; left: 0; right: 0; top: 150px;
    text-align: center; color: var(--gold-light); font-weight: 600;
  }
  .brand__name { font-size: 92px; line-height: 1; letter-spacing: 1px; }
  .brand__sub { font-size: 30px; letter-spacing: 14px; margin-top: 12px; padding-left: 14px; }
  .contact-band {
    position: absolute; left: 0; right: 0; bottom: 0; height: 152px;
    background: linear-gradient(100deg, var(--gold-deep) 0%, var(--gold) 30%, var(--gold-light) 50%, var(--gold) 70%, var(--gold-deep) 100%);
    color: var(--ink); font-weight: 600; font-size: 24px; line-height: 36px;
  }
  .contact-band__left { position: absolute; left: 36px; top: 22px; }
  .contact-band__right { position: absolute; right: 30px; top: 22px; text-align: right; }
  .contact-band__social { position: absolute; left: 498px; top: 84px; display: flex; gap: 6px; }
  .social-dot { width: 36px; height: 36px; border-radius: 50%; background: var(--ink); }
</style>
</head>
<body>
  <div class="business-card">
    <span class="corner corner--tl"></span>
    <span class="corner corner--tr"></span>
    <span class="corner corner--bl"></span>
    <span class="corner corner--br"></span>

    <div class="brand">
      <div class="brand__name">Golden Hour</div>
      <div class="brand__sub">STUDIO AND FILM</div>
    </div>

    <div class="contact-band">
      <div class="contact-band__left">
        <div>PHONE : (02) 9163 2408</div>
        <div>CELL : (04) 3187 2259</div>
        <div>INFO@TIDEWILLOWSTUDIO.NET.AU</div>
      </div>
      <div class="contact-band__social" aria-hidden="true">
        <span class="social-dot"></span>
        <span class="social-dot"></span>
      </div>
      <div class="contact-band__right">
        <div>57 TARRANT STREET</div>
        <div>GLENMORE NSW 2047</div>
        <div>TIDEWILLOWSTUDIO.NET.AU</div>
      </div>
    </div>
  </div>
</body>
</html>
```